Modern Verdell Tree Care Website

I need a website for a full service Tree Care company. The company provides tree pruning, tree removal, tree preservation, emergency services, stump grinding, and emergency tree services.

Target Market(s)

Customers that need tree services

Industry/Entity Type

Landscaping, Tree Services

Coding

Coded - Design and coding required

Number of Pages Required

5+ page

Font styles to use
Sans Serif

Requirements
Must have
• Good clean design that showcases the services the company provides.
Nice to have
• Services page; contact form, blog, home page, about page

```html
<!DOCTYPE html>
<html lang="en">
<head>
<meta charset="utf-8">
<title>Verdell Tree Care</title>
<link rel="stylesheet" href="https://fonts.googleapis.com/css2?family=Poppins:wght@400;500;600;700&display=swap">
<style>
:root{
  --green:#7cc242;
  --green-dark:#5a9a2a;
  --orange:#f9a72b;
  --heading:#56616b;
  --text:#6f7780;
  --gray-bg:#f4f4f4;
  --tint-bg:#f2f6e3;
  --footer:#0e1a10;
  --white:#ffffff;
}
*{box-sizing:border-box;margin:0;padding:0}
html,body{width:1200px;height:5075px;overflow:hidden}
body{font-family:'Poppins',sans-serif;color:var(--text);background:var(--white);position:relative}
.abs{position:absolute}
.btn{position:absolute;display:flex;align-items:center;justify-content:center;color:var(--white);font-weight:600;font-size:18px;letter-spacing:.5px;text-transform:uppercase}
.btn-orange{background:var(--orange)}
.btn-green{background:var(--green)}
.section-title{position:absolute;left:0;width:100%;text-align:center;font-size:38px;font-weight:700;color:var(--heading);text-transform:uppercase}
.brand{display:flex;align-items:center;gap:14px}
.brand-mark{width:40px;height:40px;background:var(--orange)}
.brand-name{font-size:34px;font-weight:700;color:var(--heading);white-space:nowrap}

/* header */
.header-phone{position:absolute;top:40px;display:flex;align-items:center;gap:14px}
.phone-circle{width:48px;height:48px;border-radius:50%;background:var(--green);display:flex;align-items:center;justify-content:center}
.phone-label{font-size:12px;color:var(--text)}
.phone-number{font-size:21px;font-weight:500;color:#222}
.nav{position:absolute;left:55px;top:112px;width:1095px;height:70px;background:var(--green);display:flex}
.nav a{color:var(--white);font-size:17px;text-decoration:none;display:flex;align-items:center;justify-content:center;border-right:1px solid rgba(255,255,255,.25)}
.nav .quote{margin-left:auto;width:238px;background:var(--orange);font-weight:600;font-size:21px;border:none}

/* hero */
.hero{position:absolute;left:0;top:146px;width:1200px;height:662px;background:linear-gradient(180deg,#1d3a22 0%,#2f5a2c 45%,#3f7a33 75%,#5c8f3c 100%)}
.hero-shade{position:absolute;inset:0;background:rgba(10,20,10,.45)}
.hero h1{position:absolute;top:175px;left:0;width:100%;text-align:center;color:var(--white);font-size:54px;font-weight:700;line-height:64px}
.hero h1 span{color:var(--orange);text-decoration:underline;text-underline-offset:6px}
.hero .sub{position:absolute;top:330px;width:100%;text-align:center;color:var(--white);font-size:21px;letter-spacing:.5px}

/* stats */
.stats{position:absolute;left:49px;top:709px;width:1098px;height:190px;background:var(--white);box-shadow:0 8px 30px rgba(0,0,0,.08)}
.stat{position:absolute;top:38px;display:flex;align-items:center;gap:22px}
.stat-num{font-size:68px;font-weight:700;color:var(--heading);line-height:64px}
.stat-label{font-size:22px;color:var(--heading);line-height:26px}
.grass{position:absolute;left:0;width:1200px;height:20px;background:linear-gradient(180deg,var(--green) 0%,var(--green-dark) 100%);border-radius:10px 10px 0 0}

/* who */
.gray{position:absolute;left:0;width:1200px;background:var(--gray-bg)}
.photo{position:absolute}
.who-title{position:absolute;left:575px;top:1140px;font-size:36px;font-weight:700;color:var(--heading)}
.who-text{position:absolute;left:578px;top:1208px;width:555px;font-size:13.5px;line-height:22px}

/* services */
.svc-card{position:absolute;top:1919px;width:236px;height:337px;background:var(--white);overflow:visible}
.svc-card .corner{position:absolute;right:0;bottom:0;width:0;height:0;border-left:130px solid transparent;border-bottom:200px solid #f3f3f3}
.svc-ring{position:absolute;left:46px;top:24px;width:144px;height:144px;border-radius:50%;border:3px dashed var(--green)}
.svc-img{position:absolute;left:58px;top:36px;width:120px;height:120px;border-radius:50%}
.svc-name{position:absolute;top:186px;width:100%;text-align:center;font-size:17px;font-weight:600;color:#333}
.svc-text{position:absolute;top:218px;left:18px;width:200px;text-align:center;font-size:13px;line-height:22px}
.svc-arrow{position:absolute;left:96px;top:315px;width:44px;height:44px;border-radius:50%;background:var(--orange);display:flex;align-items:center;justify-content:center}

/* why */
.why-title{position:absolute;left:59px;top:2638px;font-size:38px;font-weight:700;color:var(--heading)}
.why-text{position:absolute;left:63px;top:2693px;width:420px;font-size:13px;line-height:22px}
.feature{position:absolute;display:flex;align-items:center;gap:18px;font-size:16px;font-weight:600;color:#333;line-height:20px}
.divider{position:absolute;left:60px;width:520px;height:1px;background:#e6e6e6}

/* testimonials */
.t-card{position:absolute;top:3448px;width:422px;height:220px;background:linear-gradient(160deg,#ffffff 55%,#f3f3f3 55%)}
.stars{position:absolute;left:28px;top:22px;color:var(--green);font-size:32px;letter-spacing:4px}
.quote-badge{position:absolute;right:30px;top:20px;width:76px;height:76px;border-radius:50%;background:var(--white);box-shadow:0 4px 14px rgba(0,0,0,.08);display:flex;align-items:center;justify-content:center;color:var(--orange);font-size:64px;font-weight:700;line-height:1;padding-top:28px}
.t-name{position:absolute;left:28px;top:92px;font-size:12px;font-weight:700;color:#222}
.t-text{position:absolute;left:20px;top:125px;width:380px;font-size:12.5px;line-height:21px}

/* articles */
.post{position:absolute;top:4054px;width:284px;height:408px;background:var(--white);box-shadow:0 6px 24px rgba(0,0,0,.07)}
.post-img{position:absolute;left:0;top:0;width:284px;height:225px}
.date{position:absolute;left:22px;top:208px;width:50px;height:50px;background:var(--green);color:var(--white);text-align:center;font-size:16px;font-weight:700;line-height:18px;padding-top:7px}
.date small{display:block;font-size:9px;font-weight:500}
.post-meta{position:absolute;left:22px;top:266px;font-size:10px;color:#888}
.post-title{position:absolute;left:22px;top:292px;width:245px;font-size:17px;font-weight:500;line-height:22px;color:#333}
.read{position:absolute;left:22px;top:354px;width:108px;height:32px;background:#f2f2f2;font-size:9px;font-weight:600;color:#333;display:flex;align-items:center;justify-content:center}

/* footer */
.footer{position:absolute;left:0;top:4606px;width:1200px;height:469px;background:var(--footer)}
.f-head{position:absolute;top:106px;font-size:19px;font-weight:600;color:var(--orange)}
.f-link{position:absolute;font-size:18px;color:var(--white)}
.f-contact{position:absolute;display:flex;align-items:center;gap:14px;font-size:15px;color:var(--white)}
.f-thumb{position:absolute;width:76px;height:53px}
.f-bottom{position:absolute;top:424px;font-size:10px;color:#cfd3cf}
</style>
</head>
<body>

<!-- header -->
<div class="brand abs" style="left:58px;top:30px">
  <div class="brand-mark"></div>
  <div class="brand-name">Verdell Tree Care</div>
</div>
<div class="header-phone" style="left:510px">
  <div class="phone-circle"><svg width="22" height="22" viewBox="0 0 24 24"><path fill="#fff" d="M6.6 10.8c1.4 2.8 3.8 5.2 6.6 6.6l2.2-2.2c.3-.3.7-.4 1-.2 1.1.4 2.3.6 3.6.6.6 0 1 .4 1 1V20c0 .6-.4 1-1 1C10.6 21 3 13.4 3 4c0-.6.4-1 1-1h3.5c.6 0 1 .4 1 1 0 1.3.2 2.5.6 3.6.1.3 0 .7-.2 1z"/></svg></div>
  <div><div class="phone-label">CALL NOW</div><div class="phone-number">(555) 214 7730</div></div>
</div>
<div class="header-phone" style="left:843px">
  <div class="phone-circle"><svg width="22" height="22" viewBox="0 0 24 24"><path fill="#fff" d="M6.6 10.8c1.4 2.8 3.8 5.2 6.6 6.6l2.2-2.2c.3-.3.7-.4 1-.2 1.1.4 2.3.6 3.6.6.6 0 1 .4 1 1V20c0 .6-.4 1-1 1C10.6 21 3 13.4 3 4c0-.6.4-1 1-1h3.5c.6 0 1 .4 1 1 0 1.3.2 2.5.6 3.6.1.3 0 .7-.2 1z"/></svg></div>
  <div><div class="phone-label">CALL NOW</div><div class="phone-number">(555) 386 0412</div></div>
</div>

<!-- hero -->
<div class="hero" role="img" aria-label="Park with rounded green trees and a lawn path">
  <div class="hero-shade"></div>
  <h1>Call <span>VERDELL</span> for&nbsp; All Your<br>Tree Care Needs</h1>
  <div class="sub">SERVING LAFAYETTE AND SORROUNDING AREAS</div>
  <div class="btn btn-orange" style="left:397px;top:390px;width:204px;height:47px;font-size:17px">Our Services</div>
  <div class="btn btn-green" style="left:611px;top:390px;width:204px;height:47px;font-size:17px">Get a Quote</div>
</div>

<nav class="nav">
  <a style="width:136px">HOME</a>
  <a style="width:156px">ABOUT</a>
  <a style="width:180px">SERVICES</a>
  <a style="width:160px">BLOG</a>
  <a style="width:205px;border:none">CONTACT</a>
  <a class="quote">GET A QUOTE</a>
</nav>

<!-- gray band for who we are -->
<div class="gray" style="top:808px;height:867px"></div>

<!-- stats -->
<div class="stats">
  <div class="stat" style="left:66px">
    <svg width="92" height="96" viewBox="0 0 92 96" fill="none" stroke="#7cc242" stroke-width="3"><path d="M46 90V50M46 62l-14-10M46 58l14-12"/><path d="M24 52c-12 0-18-10-14-20 2-6 8-9 12-9 2-10 12-16 24-16s22 6 24 16c6 0 12 4 13 10 2 10-5 19-15 19z"/><path d="M30 90h32"/></svg>
    <div><div class="stat-num">5K</div><div class="stat-label">Completed<br>Projects</div></div>
  </div>
  <div class="stat" style="left:400px">
    <svg width="104" height="96" viewBox="0 0 104 96" fill="none" stroke="#7cc242" stroke-width="3"><circle cx="52" cy="34" r="28"/><circle cx="52" cy="28" r="10"/><path d="M36 52c2-9 9-13 16-13s14 4 16 13"/><path d="M18 70l5 10 11 1-8 7 2 11-10-6-10 6 2-11-8-7 11-1z M52 66l5 10 11 1-8 7 2 11-10-6-10 6 2-11-8-7 11-1z M86 70l5 10 11 1-8 7 2 11-10-6-10 6 2-11-8-7 11-1z" transform="scale(.96) translate(2 -6)"/></svg>
    <div><div class="stat-num">2K</div><div class="stat-label">Satisfied<br>Clients</div></div>
  </div>
  <div class="stat" style="left:742px">
    <svg width="96" height="96" viewBox="0 0 96 96" fill="none" stroke="#7cc242" stroke-width="3"><circle cx="48" cy="54" r="20"/><circle cx="48" cy="54" r="13"/><path d="M41 54l5 5 9-10"/><path d="M36 72l-6 20 10-4 6 8M60 72l6 20-10-4-6 8"/><path d="M48 6l3 6 6 1-4 4 1 6-6-3-6 3 1-6-4-4 6-1z M20 18l3 6 6 1-4 4 1 6-6-3-6 3 1-6-4-4 6-1z M76 18l3 6 6 1-4 4 1 6-6-3-6 3 1-6-4-4 6-1z"/></svg>
    <div><div class="stat-num">10</div><div class="stat-label">Years of<br>Experience</div></div>
  </div>
</div>
<div class="grass" style="top:890px"></div>

<!-- who we are -->
<div class="photo" role="img" aria-label="Worker cutting a large felled tree trunk with a chainsaw in the forest" style="left:83px;top:1048px;width:366px;height:398px;background:linear-gradient(135deg,#4f6e2c,#7d9a48 45%,#8a6a48 75%,#5b4433)"></div>
<div class="photo" style="left:230px;top:1249px;width:282px;height:307px;background:var(--white);box-shadow:0 6px 20px rgba(0,0,0,.1)"></div>
<div class="photo" role="img" aria-label="Gardener clearing autumn leaves with a leaf blower in a park" style="left:242px;top:1261px;width:258px;height:283px;background:linear-gradient(180deg,#3d6a2c 0%,#5d8238 45%,#b5662a 80%,#8a4420 100%)"></div>
<div class="who-title">WHO WE ARE</div>
<div class="who-text">Lorem ipsum dolor sit amet, consectetur adipiscing elit, sed do eiusmod tempor incididunt ut labore et dolore magna aliqua. Quis ipsum suspendisse ultrices gravida. Risus commodo viverra. Lorem ipsum dolor sit amet, consectetur adipiscing elit, sed do eiusmod tempor incididunt ut labore et dolore magna aliqua.</div>
<div class="btn btn-orange" style="left:575px;top:1355px;width:206px;height:46px;font-size:17px">More About Us</div>

<!-- services -->
<div class="abs" style="left:0;top:1675px;width:1200px;height:772px;background:var(--tint-bg)"></div>
<div class="section-title" style="top:1790px">OUR SERVICES</div>

<div class="svc-card" style="left:85px">
  <div class="corner"></div><div class="svc-ring"></div>
  <div class="svc-img" role="img" aria-label="Gloved hands trimming a branch" style="background:radial-gradient(circle at 40% 40%,#6f9a3d,#2f5420)"></div>
  <div class="svc-name">Tree Trimming</div>
  <div class="svc-text">Lorem ipsum dolor sit amet consectetur adipiscing,Quis ipsum suspendisse</div>
  <div class="svc-arrow"><svg width="18" height="18" viewBox="0 0 18 18"><path d="M3 9h11M9 4l5 5-5 5" stroke="#fff" stroke-width="2.5" fill="none"/></svg></div>
</div>
<div class="svc-card" style="left:355px">
  <div class="corner"></div><div class="svc-ring"></div>
  <div class="svc-img" role="img" aria-label="Chainsaw cutting through a tree" style="background:radial-gradient(circle at 60% 50%,#b5522a,#2e4a22 60%)"></div>
  <div class="svc-name">Tree Removal</div>
  <div class="svc-text">Lorem ipsum dolor sit amet consectetur adipiscing,Quis ipsum suspendisse</div>
  <div class="svc-arrow"><svg width="18" height="18" viewBox="0 0 18 18"><path d="M3 9h11M9 4l5 5-5 5" stroke="#fff" stroke-width="2.5" fill="none"/></svg></div>
</div>
<div class="svc-card" style="left:626px">
  <div class="corner"></div><div class="svc-ring"></div>
  <div class="svc-img" role="img" aria-label="Pruning shears among green leaves" style="background:radial-gradient(circle at 50% 50%,#5e8a3a,#1e3a18)"></div>
  <div class="svc-name">Tree Pruning</div>
  <div class="svc-text">Lorem ipsum dolor sit amet consectetur adipiscing,Quis ipsum suspendisse</div>
  <div class="svc-arrow"><svg width="18" height="18" viewBox="0 0 18 18"><path d="M3 9h11M9 4l5 5-5 5" stroke="#fff" stroke-width="2.5" fill="none"/></svg></div>
</div>
<div class="svc-card" style="left:898px">
  <div class="corner"></div><div class="svc-ring"></div>
  <div class="svc-img" role="img" aria-label="Fallen tree after a storm" style="background:radial-gradient(circle at 50% 40%,#9fb6a0,#4f6d3a 70%)"></div>
  <div class="svc-name">Storm Damage</div>
  <div class="svc-text">Lorem ipsum dolor sit amet consectetur adipiscing,Quis ipsum suspendisse</div>
  <div class="svc-arrow"><svg width="18" height="18" viewBox="0 0 18 18"><path d="M3 9h11M9 4l5 5-5 5" stroke="#fff" stroke-width="2.5" fill="none"/></svg></div>
</div>
<div class="btn btn-orange" style="left:493px;top:2350px;width:205px;height:46px;font-size:17px">View All</div>

<!-- why choose us -->
<div class="why-title">WHY CHOOSE US</div>
<div class="why-text">Lorem ipsum dolor sit amet consectetur adipiscing,Quis ipsum suspendisse</div>

<div class="feature" style="left:63px;top:2772px">
  <svg width="60" height="62" viewBox="0 0 60 62" fill="none" stroke="#7cc242" stroke-width="2.5"><rect x="4" y="4" width="38" height="50" rx="3"/><path d="M12 16h22M12 24h22M12 32h14"/><circle cx="44" cy="40" r="9"/><path d="M40 48l-2 10 6-3 6 3-2-10"/></svg>
  <span>Licensed and<br>Insured</span></div>
<div class="feature" style="left:321px;top:2772px">
  <svg width="66" height="62" viewBox="0 0 66 62" fill="none" stroke="#7cc242" stroke-width="2.5"><path d="M10 24a26 26 0 1 1 4 24"/><path d="M4 18l6 8 8-5"/><text x="10" y="50" font-family="Poppins,sans-serif" font-size="26" font-weight="700" fill="#7cc242" stroke="none">24</text></svg>
  <span>24 Hours<br>Emergency Services</span></div>
<div class="divider" style="top:2856px"></div>
<div class="feature" style="left:63px;top:2886px">
  <svg width="66" height="66" viewBox="0 0 66 66" fill="none" stroke="#7cc242" stroke-width="2.5"><path d="M8 54l30-38 12 6-30 38z"/><path d="M50 22l8-10"/><path d="M8 54l-4 8 10-2"/></svg>
  <span>Locally Owned<br>and Oprated</span></div>
<div class="feature" style="left:321px;top:2886px">
  <svg width="66" height="66" viewBox="0 0 66 66" fill="none" stroke="#7cc242" stroke-width="2.5"><circle cx="33" cy="14" r="8"/><circle cx="14" cy="36" r="7"/><circle cx="52" cy="36" r="7"/><path d="M21 32c2-6 7-9 12-9s10 3 12 9M4 60c1-8 5-12 10-12s9 4 10 12M42 60c1-8 5-12 10-12s9 4 10 12"/></svg>
  <span>Professional<br>Work</span></div>
<div class="divider" style="top:2972px"></div>
<div class="feature" style="left:63px;top:2998px">
  <svg width="66" height="66" viewBox="0 0 66 66" fill="none" stroke="#7cc242" stroke-width="2.5"><path d="M33 4l24 9v18c0 16-10 26-24 31C19 57 9 47 9 31V13z"/><path d="M22 33l8 8 14-16"/></svg>
  <span>Safety is our<br>First Priority</span></div>
<div class="feature" style="left:321px;top:2998px">
  <svg width="66" height="66" viewBox="0 0 66 66" fill="none" stroke="#7cc242" stroke-width="2.5"><rect x="6" y="6" width="34" height="50" rx="3"/><path d="M14 18h18M14 26h18"/><rect x="32" y="30" width="28" height="32" rx="2"/><path d="M38 38h16M38 46h4M46 46h4M54 46h0M38 54h4M46 54h4"/></svg>
  <span>Free<br>Estimates</span></div>

<div class="abs" style="left:666px;top:2604px;width:384px;height:470px;background:var(--orange)"></div>
<div class="photo" role="img" aria-label="Gloved hand pruning a dense green shrub with shears" style="left:682px;top:2626px;width:432px;height:468px;background:linear-gradient(135deg,#23421b 0%,#3f6b28 40%,#5f8d35 70%,#2a4a1e 100%)"></div>

<!-- testimonials -->
<div class="gray" style="top:3270px;height:522px"></div>
<div class="grass" style="top:3250px"></div>
<div class="section-title" style="top:3346px">HAPPY CUSTOMERS</div>
<div class="t-card" style="left:138px">
  <div class="stars">★★★★★</div><div class="quote-badge">“</div>
  <div class="t-name">ROWAN ELLIS</div>
  <div class="t-text">There are many variations of passages of Lorem Ipsum available, but the majority have suffered alteration in some form, by injected humour, randomised words .</div>
</div>
<div class="t-card" style="left:634px">
  <div class="stars">★★★★★</div><div class="quote-badge">“</div>
  <div class="t-name">ROWAN ELLIS</div>
  <div class="t-text">There are many variations of passages of Lorem Ipsum available, but the majority have suffered alteration in some form, by injected humour, randomised words .</div>
</div>

<!-- articles -->
<div class="section-title" style="top:3930px">OUR LATEST ARTICLES</div>
<div class="post" style="left:132px">
  <div class="post-img" role="img" aria-label="Seedling pots and garden trowel on a wooden table" style="background:linear-gradient(135deg,#8a6a4a,#b58a5e 50%,#6d8a3a)"></div>
  <div class="date">27<small>Feb</small></div>
  <div class="post-meta">👤 Verdell Team &nbsp;&nbsp; 💬 2 Comments</div>
  <div class="post-title">Vegetable crops that do not need pollinators</div>
  <div class="read">READ MORE →</div>
</div>
<div class="post" style="left:439px">
  <div class="post-img" role="img" aria-label="Hands holding a bowl of fresh cherry tomatoes" style="background:linear-gradient(135deg,#5d7a3a,#c9432a 50%,#7a8a5a)"></div>
  <div class="date">27<small>Feb</small></div>
  <div class="post-meta">👤 Verdell Team &nbsp;&nbsp; 💬 2 Comments</div>
  <div class="post-title">Grow your own pumpkins even in small spaces</div>
  <div class="read">READ MORE →</div>
</div>
<div class="post" style="left:747px">
  <div class="post-img" role="img" aria-label="Freshly pulled carrots held up in a garden" style="background:linear-gradient(135deg,#4a5a3a,#c9652a 50%,#3a4a6a)"></div>
  <div class="date">27<small>Feb</small></div>
  <div class="post-meta">👤 Verdell Team &nbsp;&nbsp; 💬 2 Comments</div>
  <div class="post-title">In our gardens plants for the shade garden</div>
  <div class="read">READ MORE →</div>
</div>

<!-- footer -->
<div class="grass" style="top:4572px;height:34px"></div>
<footer class="footer">
  <div class="brand abs" style="left:66px;top:96px">
    <div class="brand-mark" style="width:34px;height:34px"></div>
    <div class="brand-name" style="color:var(--white);font-size:26px">Verdell Tree Care</div>
  </div>
  <div class="abs" style="left:68px;top:166px;width:260px;font-size:17px;line-height:22px;color:var(--white)">Call VERDELL for All Your Tree Care NeedsServing Lafayette and Sorrounding Areas</div>
  <div class="abs" style="left:68px;top:320px;display:flex;gap:26px">
    <span style="width:14px;height:14px;border-radius:50%;background:var(--green)"></span>
    <span style="width:14px;height:14px;border-radius:50%;background:var(--green)"></span>
    <span style="width:14px;height:14px;border-radius:50%;background:var(--green)"></span>
  </div>

  <div class="f-head" style="left:420px">LINKS</div>
  <div class="f-link" style="left:420px;top:152px">Home</div>
  <div class="f-link" style="left:420px;top:192px">About</div>
  <div class="f-link" style="left:420px;top:232px">Services</div>
  <div class="f-link" style="left:420px;top:272px">Blog</div>
  <div class="f-link" style="left:420px;top:312px">Contact</div>

  <div class="f-head" style="left:605px">GALLERY</div>
  <div class="f-thumb" role="img" aria-label="Garden lawn" style="left:600px;top:166px;background:linear-gradient(135deg,#4f7a34,#9ab86a)"></div>
  <div class="f-thumb" role="img" aria-label="Leafy hedge" style="left:682px;top:166px;background:linear-gradient(135deg,#2e5a22,#6f9a42)"></div>
  <div class="f-thumb" role="img" aria-label="Tree planting" style="left:600px;top:225px;background:linear-gradient(135deg,#3a4a2a,#8a5a3a)"></div>
  <div class="f-thumb" role="img" aria-label="Garden path" style="left:682px;top:225px;background:linear-gradient(135deg,#5a7a3a,#3a5a2a)"></div>

  <div class="f-head" style="left:892px">CONTACT</div>
  <div class="f-contact" style="left:892px;top:158px"><svg width="20" height="20" viewBox="0 0 24 24"><path fill="#7cc242" d="M6.6 10.8c1.4 2.8 3.8 5.2 6.6 6.6l2.2-2.2c.3-.3.7-.4 1-.2 1.1.4 2.3.6 3.6.6.6 0 1 .4 1 1V20c0 .6-.4 1-1 1C10.6 21 3 13.4 3 4c0-.6.4-1 1-1h3.5c.6 0 1 .4 1 1 0 1.3.2 2.5.6 3.6.1.3 0 .7-.2 1z"/></svg>(555) 214 7730</div>
  <div class="f-contact" style="left:892px;top:218px"><svg width="20" height="20" viewBox="0 0 24 24"><path fill="#7cc242" d="M6.6 10.8c1.4 2.8 3.8 5.2 6.6 6.6l2.2-2.2c.3-.3.7-.4 1-.2 1.1.4 2.3.6 3.6.6.6 0 1 .4 1 1V20c0 .6-.4 1-1 1C10.6 21 3 13.4 3 4c0-.6.4-1 1-1h3.5c.6 0 1 .4 1 1 0 1.3.2 2.5.6 3.6.1.3 0 .7-.2 1z"/></svg>(555) 386 0412</div>
  <div class="f-contact" style="left:892px;top:278px"><svg width="20" height="22" viewBox="0 0 24 26"><path fill="#7cc242" d="M12 1a8 8 0 0 0-8 8c0 6 8 15 8 15s8-9 8-15a8 8 0 0 0-8-8zm0 11a3 3 0 1 1 0-6 3 3 0 0 1 0 6z"/></svg>48 Birchwood Lane, Oakridge</div>

  <div class="abs" style="left:60px;top:412px;width:1080px;height:1px;background:rgba(255,255,255,.12)"></div>
  <div class="f-bottom" style="left:72px">Copyright © 2024 Verdell Tree Care. All Rights Reserved</div>
  <div class="f-bottom" style="right:72px">Privacy Policy | Terms and Conditions</div>
</footer>

</body>
</html>
```